I am a general contractor in Portland, Or. I would like a clean and simple design layout, maybe using the "didot" font, blue and dark bronze in colors are preferred. On one side of the card, it would be nice to have a logo(attached photo) and business name(KTW Construction). I don't need my job title on the card, just some thing along the lines of "gordon pike, general contractor". Thanks much.

Target Market(s)

Adults from 30-55 years old. Middle to upper class.

Industry/Entity Type

Contractor

Contact Information for Business Card

KTW Construction
Gordon L. Pike
2843 NE 71st Ave.
Portland, Or. 97288
541.555.0187

Font styles to use
Other font styles liked:
• didot

Colors
3277b5
7f7f7f

Requirements
Should not have
• Too much going on.

```html
<!DOCTYPE html>
<html lang="en">
<head>
<meta charset="utf-8">
<title>KTW Construction – Business Card</title>
<link rel="stylesheet" href="https://fonts.googleapis.com/css2?family=Ubuntu:wght@400;500&display=swap">
<style>
  :root {
    --backdrop: #e8e4dc;
    --card-light: #fbfbfb;
    --card-shade: #dedede;
    --brand-blue: #2aa3dc;
    --ink-dark: #1e1e1e;
    --ink-grey: #4a4a4a;
    --white: #ffffff;
  }
  * { box-sizing: border-box; margin: 0; padding: 0; }
  html, body {
    width: 1057px;
    height: 1200px;
    overflow: hidden;
    background: var(--backdrop);
    font-family: "Ubuntu", sans-serif;
  }
  .sheet {
    position: relative;
    width: 1057px;
    height: 1200px;
  }
  .card {
    position: absolute;
    left: 128px;
    width: 800px;
    height: 457px;
    background: radial-gradient(ellipse at 35% 40%, var(--card-light) 0%, #f0f0f0 55%, var(--card-shade) 100%);
    box-shadow: 0 6px 18px rgba(0,0,0,0.18);
    overflow: hidden;
  }
  .card--front { top: 100px; }
  .card--back { top: 643px; }

  .brand {
    display: flex;
    align-items: center;
    gap: 18px;
    white-space: nowrap;
  }
  .brand__dot {
    width: 58px;
    height: 58px;
    border-radius: 50%;
    background: var(--ink-dark);
    flex: none;
  }
  .brand__name {
    color: var(--brand-blue);
    font-weight: 500;
    font-size: 46px;
    letter-spacing: 0.5px;
  }
  .card--front .brand {
    position: absolute;
    left: 50%;
    top: 50%;
    transform: translate(-50%, -50%);
  }
  .card--back .brand {
    position: absolute;
    left: 60px;
    top: 70px;
  }
  .card--back .brand__dot { width: 48px; height: 48px; }
  .card--back .brand__name { font-size: 36px; }

  .nameplate {
    position: absolute;
    right: 0;
    top: 56px;
    width: 330px;
    height: 104px;
    background: var(--ink-dark);
    border-top: 6px solid var(--brand-blue);
    border-bottom: 6px solid var(--brand-blue);
    color: var(--white);
    display: flex;
    flex-direction: column;
    justify-content: center;
    padding-left: 40px;
    white-space: nowrap;
  }
  .nameplate__name {
    font-size: 30px;
    font-weight: 500;
    letter-spacing: 1px;
  }
  .nameplate__title {
    font-size: 15px;
    letter-spacing: 2px;
    margin-top: 4px;
  }

  .contact-list {
    position: absolute;
    left: 60px;
    top: 250px;
    list-style: none;
  }
  .contact-list__item {
    display: flex;
    align-items: flex-start;
    gap: 16px;
    margin-bottom: 18px;
    color: var(--ink-grey);
    font-size: 17px;
    line-height: 24px;
  }
  .contact-list__icon {
    width: 24px;
    height: 24px;
    flex: none;
  }
  .contact-list__lines {
    display: flex;
    flex-direction: column;
  }
</style>
</head>
<body>
<main class="sheet">

  <section class="card card--front" aria-label="Card front">
    <div class="brand">
      <span class="brand__dot" aria-hidden="true"></span>
      <span class="brand__name">KTW Construction</span>
    </div>
  </section>

  <section class="card card--back" aria-label="Card back">
    <div class="brand">
      <span class="brand__dot" aria-hidden="true"></span>
      <span class="brand__name">KTW Construction</span>
    </div>

    <div class="nameplate">
      <span class="nameplate__name">GORDON PIKE</span>
      <span class="nameplate__title">GENERAL CONTRACTOR</span>
    </div>

    <ul class="contact-list">
      <li class="contact-list__item">
        <svg class="contact-list__icon" viewBox="0 0 24 24" aria-hidden="true">
          <rect width="24" height="24" rx="3" fill="#1e1e1e"/>
          <path d="M8 6h3l1 3-2 1.5a8 8 0 0 0 3.5 3.5L15 12l3 1v3a2 2 0 0 1-2 2A10 10 0 0 1 6 8a2 2 0 0 1 2-2z" fill="#fff"/>
        </svg>
        <span>541.555.0187</span>
      </li>
      <li class="contact-list__item">
        <svg class="contact-list__icon" viewBox="0 0 24 24" aria-hidden="true">
          <rect width="24" height="24" rx="3" fill="#1e1e1e"/>
          <path d="M12 19s-5-5.2-5-8.6a5 5 0 0 1 10 0C17 13.8 12 19 12 19z" fill="#fff"/>
          <circle cx="12" cy="10.5" r="1.8" fill="#1e1e1e"/>
        </svg>
        <span class="contact-list__lines">
          <span>2843 NE 71st Ave.</span>
          <span>Portland, Or. 97288</span>
        </span>
      </li>
    </ul>
  </section>

</main>
</body>
</html>
```